Business Card Design

Hi I need a business card designed, we already have the business name logo artwork and would like some concept ideas for the Bus Card layout.
On the back of the card i want to include the products and services that we offer.
We are a Plastics Sheeting manufacture based in Perth Australia.

                                       

We need a BC design for a company called Tarvo Plastics based in Perth Australia.

We supply from DIY to Trade & Industrial  Engineering Markets.

We specialise in:

·         Cut to size panels  (all shapes and sizes)

·         Plastics fabrication & Welding

·         Custom Designs

·         Plastic Repairs

·         PVC Pipe Slotting & PVC Pipe Threading

·         Supplier of all types of engineering plastics and profiles.

Including:           Acrylic / Clarvene

                               Polycarbonate / Dorvil

                               Prismatic Light Diffuser

                               Vantrib

                               HDPE / UHMWPE

                               PVC / PVC Foam

                               Nylon

                               HIPS

```html
<!DOCTYPE html>
<html lang="en">
<head>
<meta charset="utf-8">
<title>Tarvo Plastics Business Card</title>
<link rel="stylesheet" href="https://fonts.googleapis.com/css2?family=Open+Sans:ital,wght@0,400;0,600;0,700;0,800;1,700&display=swap">
<style>
  :root {
    --bg: #e9e9ee;
    --card: #ffffff;
    --navy: #1b2a6b;
    --orange: #e87722;
    --ink: #3a3a3a;
    --rule: #c9c9c9;
  }
  * { box-sizing: border-box; margin: 0; padding: 0; }
  html, body { width: 1200px; height: 987px; overflow: hidden; }
  body {
    background: var(--bg);
    font-family: "Open Sans", Arial, sans-serif;
    color: var(--ink);
    position: relative;
  }
  .card {
    position: absolute;
    left: 215px;
    width: 770px;
    height: 440px;
    background: var(--card);
    border-radius: 28px;
    box-shadow: 0 6px 18px rgba(0,0,0,0.12);
    overflow: hidden;
  }
  .card--front { top: 34px; }
  .card--back { top: 512px; }

  .brand {
    font-weight: 800;
    color: var(--navy);
    letter-spacing: -0.5px;
    display: flex;
    align-items: center;
    gap: 14px;
    white-space: nowrap;
  }
  .brand__mark {
    width: 22px; height: 22px;
    background: var(--navy);
    display: inline-block;
  }

  /* Front */
  .card--front .brand {
    position: absolute;
    left: 0; right: 0; top: 62px;
    justify-content: center;
    font-size: 70px;
  }
  .front__rule {
    position: absolute;
    left: 70px; right: 70px; top: 182px;
    height: 2px;
    background: linear-gradient(90deg, transparent, var(--rule) 15%, var(--rule) 85%, transparent);
  }
  .person {
    position: absolute;
    left: 0; right: 0; top: 206px;
    text-align: center;
    font-size: 25px;
    font-weight: 700;
    color: var(--navy);
  }
  .person__title { color: var(--orange); font-weight: 400; }
  .contact {
    position: absolute;
    left: 0; right: 0; top: 258px;
    text-align: center;
    font-size: 19px;
    line-height: 1.6;
  }
  .contact__row { display: flex; justify-content: center; align-items: center; gap: 8px; }
  .icon { width: 17px; height: 17px; fill: var(--orange); flex: none; }
  .contact__sep { width: 10px; }
  .legal { font-size: 16px; margin-top: 4px; }

  /* Back */
  .card--back .brand {
    position: absolute;
    right: 50px; top: 34px;
    font-size: 50px;
  }
  .tagline {
    position: absolute;
    left: 50px; right: 50px; top: 112px;
    text-align: center;
    font-size: 19px;
    font-weight: 700;
    font-style: italic;
    color: var(--navy);
    line-height: 1.35;
  }
  .lists {
    position: absolute;
    left: 50px; right: 50px; top: 190px;
    display: grid;
    grid-template-columns: 1.2fr 1px 1fr;
    column-gap: 30px;
  }
  .lists__divider { background: var(--rule); }
  .lists h2 {
    font-size: 21px;
    font-weight: 700;
    color: var(--navy);
    margin-bottom: 6px;
  }
  .lists ul { list-style: none; font-size: 15.5px; line-height: 1.42; }
  .lists li { position: relative; padding-left: 16px; }
  .lists li::before,
  .pair::before {
    content: "";
    position: absolute; left: 2px; top: 8px;
    width: 7px; height: 7px;
    border-radius: 50%;
    background: var(--orange);
  }
  .materials li { white-space: nowrap; }
  .pair {
    position: relative;
    display: inline-block;
    margin-left: 18px;
    padding-left: 16px;
  }
</style>
</head>
<body>

<section class="card card--front" aria-label="Business card front">
  <div class="brand"><span class="brand__mark"></span>Tarvo Plastics</div>
  <div class="front__rule"></div>
  <p class="person">Your Name, <span class="person__title">Title</span></p>
  <div class="contact">
    <p>Unit 4/18 Harlow Circuit Bremford WA 6158</p>
    <p>PO Box 2740 Bremford DC WA 6972</p>
    <p class="contact__row">
      <svg class="icon" viewBox="0 0 24 24" aria-hidden="true"><path d="M6.6 10.8a15.2 15.2 0 0 0 6.6 6.6l2.2-2.2a1 1 0 0 1 1-.25 11.4 11.4 0 0 0 3.6.57 1 1 0 0 1 1 1V20a1 1 0 0 1-1 1A17 17 0 0 1 3 4a1 1 0 0 1 1-1h3.5a1 1 0 0 1 1 1c0 1.25.2 2.45.57 3.6a1 1 0 0 1-.25 1z"/></svg>
      <span>08 9471 3305</span><span class="contact__sep"></span>
      <svg class="icon" viewBox="0 0 24 24" aria-hidden="true"><path d="M7 1h10a2 2 0 0 1 2 2v18a2 2 0 0 1-2 2H7a2 2 0 0 1-2-2V3a2 2 0 0 1 2-2zm0 3v14h10V4zm5 15.5a1.2 1.2 0 1 0 0 2.4 1.2 1.2 0 0 0 0-2.4z"/></svg>
      <span>0400 555 182</span><span class="contact__sep"></span>
      <svg class="icon" viewBox="0 0 24 24" aria-hidden="true"><path d="M6 2h9l3 3v4h1a3 3 0 0 1 3 3v7a2 2 0 0 1-2 2H4a2 2 0 0 1-2-2v-7a3 3 0 0 1 3-3h1zm2 2v5h8V6h-2V4zm-1 9v2h10v-2z"/></svg>
      <span>08 9471 3306</span>
    </p>
    <p class="contact__row legal">
      <svg class="icon" viewBox="0 0 24 24" aria-hidden="true"><path d="M2 5h20v14H2zm2 2v.5l8 5.5 8-5.5V7zm0 2.9V17h16V9.9l-8 5.5z"/></svg>
      <span>sales@tarvoplastics.com.au &nbsp;|&nbsp; Keldmoor Holdings Pty Ltd T/A Tarvo Plastics ABN: TBA</span>
    </p>
  </div>
</section>

<section class="card card--back" aria-label="Business card back">
  <div class="brand"><span class="brand__mark"></span>Tarvo Plastics</div>
  <p class="tagline">The Products And Services That We Offer<br>Are Supplied From Diy To Trade &amp; Industrial Engineering Markets</p>
  <div class="lists">
    <div>
      <h2>We specialise in:</h2>
      <ul>
        <li>Cut to size panels (all shapes and sizes)</li>
        <li>Plastics fabrication &amp; Welding</li>
        <li>Custom Designs</li>
        <li>Plastic Repairs</li>
        <li>PVC Pipe Slotting &amp; PVC Pipe Threading</li>
        <li>Supplier of all types of engineering plastics and profiles</li>
      </ul>
    </div>
    <div class="lists__divider"></div>
    <div>
      <h2>Including:</h2>
      <ul class="materials">
        <li>Acrylic / Clarvene</li>
        <li>Polycarbonate / Dorvil</li>
        <li>Prismatic Light Diffuser</li>
        <li>Vantrib <span class="pair">HDPE / UHMWPE</span></li>
        <li>PVC / PVC Foam</li>
        <li>Nylon <span class="pair">HIPS</span></li>
      </ul>
    </div>
  </div>
</section>

</body>
</html>
```